Product Description Graphic

We are designing a new product and need a better graphic to describe it.

We are not worried about names of the modules yet but want to be descriptive of capabilities. Right now "Present & CMA" should really be "Presentations & CMA".

I overall like the shape of the triangle and the arrow for Contacts but this is a very unsophisticated graphic done by a non-designer. Also need to better show that each block of capabilites will also have paywall capabilities.

Target Market(s)

Real Estate Brokerage Firms and Real Estate Agents

Industry/Entity Type

Real Estate

Colors

Designer to choose colors to be used in the design.

Requirements
Must have
• Sophisticated design. Paywall description embedded.

```html
<!DOCTYPE html>
<html lang="en">
<head>
<meta charset="utf-8">
<title>Product Capabilities Wheel</title>
<link href="https://fonts.googleapis.com/css2?family=Nunito+Sans:wght@700;800&display=swap" rel="stylesheet">
<style>
  :root {
    --canvas: #ffffff;
    --track: #e2e2e2;
    --label: #0b6cc0;
    --ink: #111111;
    --hatch-line: #3a2d6b;
    --email-core: #0275e4;
    --email-band: #0095da;
    --present-core: #1a88e4;
    --present-band: #24a9d6;
    --mobile-core: #00a2f7;
    --mobile-band: #00bcf7;
    --web-core: #34adf0;
    --web-band: #52c4ec;
    --extra-core: #5ea8e6;
    --extra-band: #9abfdd;
    --contacts: #5ea8e8;
    --contacts-text: #1a6fc0;
  }
  html, body {
    margin: 0;
    padding: 0;
    overflow: hidden;
    background: var(--canvas);
  }
  .canvas {
    width: 1200px;
    height: 1200px;
    display: block;
    font-family: "Nunito Sans", "Avenir Next", Arial, sans-serif;
  }
  .track { fill: var(--track); }
  .gap { stroke: var(--track); stroke-width: 24; }
  .module-label {
    fill: var(--label);
    font-size: 27px;
    font-weight: 800;
    letter-spacing: 0.5px;
  }
  .hub-label {
    fill: var(--contacts-text);
    font-size: 21px;
    font-weight: 800;
  }
  .legend-mark { stroke: #555; stroke-width: 1.2; }
  .legend-text {
    fill: var(--ink);
    font-size: 16px;
    font-weight: 800;
  }
</style>
</head>
<body>
<svg class="canvas" viewBox="0 0 1200 1200" xmlns="http://www.w3.org/2000/svg">
  <defs>
    <pattern id="paywall-hatch" width="22" height="22" patternUnits="userSpaceOnUse" patternTransform="rotate(-45)">
      <line x1="0" y1="0" x2="0" y2="22" stroke="var(--hatch-line)" stroke-width="1.3"/>
    </pattern>
    <path id="arc-top" d="M 295 600 A 305 305 0 0 1 905 600"/>
    <path id="arc-bottom" d="M 270 600 A 330 330 0 0 0 930 600"/>
  </defs>

  <!-- outer track -->
  <circle class="track" cx="600" cy="600" r="340"/>

  <!-- paywall bands -->
  <g class="paywall-bands">
    <path fill="var(--present-band)" d="M600 600 L600 310 A290 290 0 0 1 890 600 Z"/>
    <path fill="var(--mobile-band)" d="M600 600 L890 600 A290 290 0 0 1 708.6 868.9 Z"/>
    <path fill="var(--extra-band)" d="M600 600 L708.6 868.9 A290 290 0 0 1 600 890 Z"/>
    <path fill="var(--web-band)" d="M600 600 L600 890 A290 290 0 0 1 394.9 805.1 Z"/>
    <path fill="var(--email-band)" d="M600 600 L394.9 805.1 A290 290 0 0 1 600 310 Z"/>
    <circle cx="600" cy="600" r="290" fill="url(#paywall-hatch)"/>
  </g>

  <!-- module cores -->
  <g class="module-cores">
    <path fill="var(--present-core)" d="M600 600 L600 360 A240 240 0 0 1 840 600 Z"/>
    <path fill="var(--mobile-core)" d="M600 600 L840 600 A240 240 0 0 1 689.9 822.5 Z"/>
    <path fill="var(--extra-core)" d="M600 600 L689.9 822.5 A240 240 0 0 1 600 840 Z"/>
    <path fill="var(--web-core)" d="M600 600 L600 840 A240 240 0 0 1 430.3 769.7 Z"/>
    <path fill="var(--email-core)" d="M600 600 L430.3 769.7 A240 240 0 0 1 600 360 Z"/>
  </g>

  <!-- separators -->
  <g class="gaps">
    <line class="gap" x1="600" y1="600" x2="600" y2="300"/>
    <line class="gap" x1="600" y1="600" x2="900" y2="600"/>
    <line class="gap" x1="600" y1="600" x2="712.4" y2="878.2"/>
    <line class="gap" x1="600" y1="600" x2="600" y2="900"/>
    <line class="gap" x1="600" y1="600" x2="387.9" y2="812.1"/>
  </g>

  <!-- contacts hub -->
  <circle class="track" cx="600" cy="600" r="148"/>
  <circle cx="600" cy="600" r="122" fill="var(--contacts)"/>
  <text class="hub-label" x="600" y="608" text-anchor="middle">CONTACTS</text>

  <!-- module labels -->
  <text class="module-label" text-anchor="middle"><textPath href="#arc-top" startOffset="158">Email Nateure Print</textPath></text>
  <text class="module-label" text-anchor="middle"><textPath href="#arc-top" startOffset="722">Presentations</textPath></text>
  <text class="module-label" text-anchor="middle"><textPath href="#arc-bottom" startOffset="362">Websites &amp; Leads</textPath></text>
  <text class="module-label" text-anchor="middle"><textPath href="#arc-bottom" startOffset="818">Mobile</textPath></text>

  <!-- legend -->
  <g class="legend">
    <line class="legend-mark" x1="880" y1="970" x2="905" y2="995"/>
    <line class="legend-mark" x1="908" y1="970" x2="930" y2="992"/>
    <line class="legend-mark" x1="872" y1="992" x2="906" y2="1026"/>
    <line class="legend-mark" x1="896" y1="996" x2="928" y2="1028"/>
    <line class="legend-mark" x1="872" y1="1020" x2="878" y2="1026"/>
    <text class="legend-text" x="962" y="993">Paywall</text>
    <text class="legend-text" x="962" y="1025">Feature</text>
  </g>
</svg>
</body>
</html>
```